International Petrochemical business needs a web design for Clearway Desk system

We need a web design for a "Clearway Desk" system for an international petrochemical company. The web site is used internally within the company. It is hosted by an internal department which provides government permit request service for other departments.

We would like to see designs of two pages using color light blue. (home page, internal page as attached).
Home Page:
1. Header has a background image and small animation. Header on home page can be taller than the header of the internal page.
2. Layout as attached.

Internal Page:
1. Header can use the same background image as the home page and can be shorter to utilize the page for content.
2. The blue icon behind every captions represent an icon. When user move mouse over this icon, it displays the caption in Thai language as a tooltip. This icon needs to be redesign.

The final design should communicate the followings:
- Excellent service provided system in terms of time and accurary
- Rapid growth of business via building petrochemical refinery plant
Updates

For Internal Page, the blue circle behind every captions represent an icon. When mouse over this icon, a tool tip showing the caption in Thai language is shown. Please also design this icon..

There are more feedbacks from customer as followed:

1. Banner should consists of 
    1.1 "Approved" stamp on paper
    1.2 An image of Garuda. It is used on every government documents in Thailand
    1.3 Image of petrochemical plant
2. Each menu item (Home, Permit, Search, etc) should have different colors. Drop down menu will use the same color as its parent menu item.
3. Overall tone of the web page should be light blue with background of the body the web page in white
4. "New Request" button should use green color with icon on it
5. Table header of each box in the body of the page should use dark blue background with text in white

Please kindly submit your revisions.
Thank you.

Industry/Entity Type

Business

Requirements
Must have
• 1. Design for 1024x768 screen resolution
2. Use light blue theme
3. Background of header where the company logo is must have white background

```html
<!DOCTYPE html>
<html lang="en">
<head>
<meta charset="utf-8">
<title>Clearway Desk – Home</title>
<link href="https://fonts.googleapis.com/css2?family=Oswald:wght@300;400&family=Open+Sans:wght@400;600&display=swap" rel="stylesheet">
<style>
:root{
  --sky:#1ab8f0;
  --sky-text:#12a9e3;
  --navy:#1f3a6e;
  --brand:#2a2a6e;
  --green:#3aaa4a;
  --ink:#333;
  --muted:#888;
  --panel:#fcfcfc;
  --pager:#f4f4f4;
  --line:#e6e6e6;
  --btn:#d3d3d3;
  --white:#fff;
  --nav-home:#1ab8f0;
  --nav-permits:#e58a1f;
  --nav-search:#3aaa4a;
  --nav-report:#8a4fc2;
  --nav-admin:#d8434a;
  --nav-help:#1f8f9a;
}
*{box-sizing:border-box;margin:0;padding:0}
html,body{width:1200px;height:625px;overflow:hidden;background:var(--white)}
body{font-family:"Open Sans",Arial,sans-serif;color:var(--ink)}
.stage{position:relative;width:1384px;height:781px;transform:translate(-160px,0) scale(.8);transform-origin:0 0;margin-left:0}
.abs{position:absolute}

.brand{left:236px;top:14px;display:flex;align-items:center;gap:10px}
.brand-dot{width:38px;height:38px;border-radius:50%;background:var(--sky)}
.brand-name{font-family:"Oswald",sans-serif;font-weight:400;color:var(--brand);font-size:20px;line-height:21px;width:140px}

.nav{left:656px;top:29px;display:flex;height:31px;font-family:"Oswald",sans-serif;font-weight:300;font-size:21px}
.nav a{display:flex;align-items:center;text-decoration:none;padding:0 17px;border-left:1px dotted #bbb;border-bottom:3px solid currentColor}
.nav a:first-child,.nav a:nth-child(2){border-left:none}
.nav .home{color:var(--white);background:var(--nav-home);border-bottom-color:var(--nav-home)}
.nav .permits{color:var(--nav-permits)}
.nav .search{color:var(--nav-search)}
.nav .report{color:var(--nav-report)}
.nav .admin{color:var(--nav-admin)}
.nav .help{color:var(--nav-help)}
.nav .caret{margin-left:10px}

.banner{left:217px;top:72px;width:967px;height:64px;background:linear-gradient(90deg,#dff4fd 0%,#b9e6f8 45%,#8fd3f2 100%)}

.panel{background:var(--panel);border:1px solid var(--line);border-top:none}
.panel-head{height:26px;line-height:26px;padding-left:20px;color:var(--white);font-weight:600;font-size:16px;background:var(--sky)}
.grid{width:100%;border-collapse:collapse;font-size:12px;table-layout:fixed}
.grid th{background:var(--navy);color:var(--white);font-weight:600;font-size:14px;text-align:left;height:25px;vertical-align:middle}
.grid td{height:21px;vertical-align:middle}
.grid th:first-child,.grid td:first-child{padding-left:20px}
.grid .num{text-align:right}
.grid .end{padding-right:40px}
.pager{position:absolute;left:0;right:0;bottom:0;height:43px;background:var(--pager);display:flex;align-items:center;justify-content:center;font-size:12px;color:var(--muted)}
.pbtn{width:27px;height:25px;border-radius:3px;background:var(--btn);display:flex;align-items:center;justify-content:center}
.pfirst{margin-right:34px}
.plast{margin-left:49px}
.pinfo{display:flex;align-items:center;gap:9px;margin:0 9px}
.pbox{width:27px;height:17px;border:1px solid #bbb;background:var(--white);font-size:11px;text-align:center;line-height:15px;color:var(--muted)}
.scroll{position:absolute;top:54px;bottom:8px;border-left:1px dotted #555}
.thumb{position:absolute;left:-4px;top:4px;width:7px;height:40px;border-radius:3px;background:#777}

.new-btn{left:850px;top:515px;width:334px;height:45px;background:var(--green);color:var(--white);font-family:"Oswald",sans-serif;font-weight:400;font-size:27px;display:flex;align-items:center;justify-content:center;gap:12px;text-decoration:none}

.footer{left:221px;top:738px;font-size:12px;color:#555}
.social{left:1066px;top:730px;display:flex;gap:7px}
.social span{width:24px;height:24px;border-radius:3px;background:#ccc}
</style>
</head>
<body>
<div class="stage">

<div class="abs brand"><span class="brand-dot"></span><span class="brand-name">Norvane Petrochemical</span></div>

<nav class="abs nav">
  <a class="home" href="#">HOME</a>
  <a class="permits" href="#">PERMITS<svg class="caret" width="14" height="9" viewBox="0 0 14 9"><path d="M0 0h14L7 9z" fill="currentColor"/></svg></a>
  <a class="search" href="#">SEARCH</a>
  <a class="report" href="#">REPORT</a>
  <a class="admin" href="#">ADMIN</a>
  <a class="help" href="#">HELP</a>
</nav>

<div class="abs banner" role="img" aria-label="Header banner: approved stamp on a permit paper, government emblem and petrochemical plant"></div>

<section class="abs panel" style="left:217px;top:150px;width:476px;height:170px">
  <div class="panel-head">New Request</div>
  <table class="grid"><colgroup><col style="width:128px"><col style="width:124px"><col></colgroup>
    <tr><th>Request No.</th><th>Request Date</th><th>Branch</th></tr>
    <tr><td>56-0003</td><td>20/4/2013</td><td>GC1</td></tr>
    <tr><td>56-0003</td><td>21/4/2013</td><td>GC2</td></tr>
    <tr><td>56-0003</td><td>22/4/2013</td><td>GC3</td></tr>
  </table>
  <div class="pager">
    <span class="pbtn pfirst"><svg width="20" height="14"><path d="M10 1L4 7l6 6M17 1l-6 6 6 6" stroke="#555" stroke-width="2.5" fill="none"/></svg></span>
    <span class="pbtn"><svg width="12" height="14"><path d="M9 1L3 7l6 6" stroke="#555" stroke-width="2.5" fill="none"/></svg></span>
    <span class="pinfo">Page <span class="pbox">1</span> of 1</span>
    <span class="pbtn"><svg width="12" height="14"><path d="M3 1l6 6-6 6" stroke="#555" stroke-width="2.5" fill="none"/></svg></span>
    <span class="pbtn plast"><svg width="20" height="14"><path d="M3 1l6 6-6 6M10 1l6 6-6 6" stroke="#555" stroke-width="2.5" fill="none"/></svg></span>
  </div>
  <div class="scroll" style="left:464px"><div class="thumb"></div></div>
</section>

<section class="abs panel" style="left:709px;top:150px;width:475px;height:170px">
  <div class="panel-head">My Working Request</div>
  <table class="grid"><colgroup><col style="width:128px"><col style="width:124px"><col></colgroup>
    <tr><th>Request No.</th><th>Request Date</th><th>Branch</th></tr>
    <tr><td>56-0003</td><td>20/4/2013</td><td>waiting for process</td></tr>
    <tr><td>56-0003</td><td>21/4/2013</td><td>In Progress</td></tr>
    <tr><td>56-0003</td><td>22/4/2013</td><td>in complete document</td></tr>
  </table>
  <div class="pager">
    <span class="pbtn pfirst"><svg width="20" height="14"><path d="M10 1L4 7l6 6M17 1l-6 6 6 6" stroke="#555" stroke-width="2.5" fill="none"/></svg></span>
    <span class="pbtn"><svg width="12" height="14"><path d="M9 1L3 7l6 6" stroke="#555" stroke-width="2.5" fill="none"/></svg></span>
    <span class="pinfo">Page <span class="pbox">1</span> of 1</span>
    <span class="pbtn"><svg width="12" height="14"><path d="M3 1l6 6-6 6" stroke="#555" stroke-width="2.5" fill="none"/></svg></span>
    <span class="pbtn plast"><svg width="20" height="14"><path d="M3 1l6 6-6 6M10 1l6 6-6 6" stroke="#555" stroke-width="2.5" fill="none"/></svg></span>
  </div>
  <div class="scroll" style="left:464px"><div class="thumb"></div></div>
</section>

<section class="abs panel" style="left:217px;top:331px;width:967px;height:170px">
  <div class="panel-head">Expiring Permits</div>
  <table class="grid"><colgroup><col style="width:128px"><col style="width:314px"><col style="width:200px"><col style="width:150px"><col></colgroup>
    <tr><th>Permit No.</th><th>Expire Date</th><th>Branch</th><th class="num">Required Time (Day)</th><th class="num end">Due Dated</th></tr>
    <tr><td>56-0003</td><td>20/4/2013</td><td>GC1</td><td class="num">30</td><td class="num end">-40</td></tr>
    <tr><td>56-0003</td><td>21/4/2013</td><td>GC2</td><td class="num">60</td><td class="num end">15</td></tr>
    <tr><td>56-0003</td><td>22/4/2013</td><td>GC3</td><td class="num">50</td><td class="num end">25</td></tr>
  </table>
  <div class="pager">
    <span class="pbtn pfirst"><svg width="20" height="14"><path d="M10 1L4 7l6 6M17 1l-6 6 6 6" stroke="#555" stroke-width="2.5" fill="none"/></svg></span>
    <span class="pbtn"><svg width="12" height="14"><path d="M9 1L3 7l6 6" stroke="#555" stroke-width="2.5" fill="none"/></svg></span>
    <span class="pinfo">Page <span class="pbox">1</span> of 1</span>
    <span class="pbtn"><svg width="12" height="14"><path d="M3 1l6 6-6 6" stroke="#555" stroke-width="2.5" fill="none"/></svg></span>
    <span class="pbtn plast"><svg width="20" height="14"><path d="M3 1l6 6-6 6M10 1l6 6-6 6" stroke="#555" stroke-width="2.5" fill="none"/></svg></span>
  </div>
  <div class="scroll" style="left:955px"><div class="thumb"></div></div>
</section>

<section class="abs panel" style="left:217px;top:515px;width:624px;height:201px">
  <div class="panel-head">My In Progress Requests</div>
  <table class="grid"><colgroup><col style="width:167px"><col style="width:146px"><col></colgroup>
    <tr><th>Request No.</th><th>Requested</th><th>Status</th></tr>
    <tr><td>56-0003</td><td>20/4/2013</td><td>lorem ipsum dolor sit amtem dotem totun khabun</td></tr>
    <tr><td style="height:33px">56-0003</td><td>20/4/2013</td><td>lorem ipsum dolor sit amtem dotem totun khabun</td></tr>
  </table>
  <div class="pager">
    <span class="pbtn pfirst"><svg width="20" height="14"><path d="M10 1L4 7l6 6M17 1l-6 6 6 6" stroke="#555" stroke-width="2.5" fill="none"/></svg></span>
    <span class="pbtn"><svg width="12" height="14"><path d="M9 1L3 7l6 6" stroke="#555" stroke-width="2.5" fill="none"/></svg></span>
    <span class="pinfo">Page <span class="pbox">1</span> of 1</span>
    <span class="pbtn"><svg width="12" height="14"><path d="M3 1l6 6-6 6" stroke="#555" stroke-width="2.5" fill="none"/></svg></span>
    <span class="pbtn plast"><svg width="20" height="14"><path d="M3 1l6 6-6 6M10 1l6 6-6 6" stroke="#555" stroke-width="2.5" fill="none"/></svg></span>
  </div>
</section>

<a class="abs new-btn" href="#"><svg width="24" height="24" viewBox="0 0 24 24"><circle cx="12" cy="12" r="11" fill="none" stroke="#fff" stroke-width="2"/><path d="M12 6v12M6 12h12" stroke="#fff" stroke-width="2.5"/></svg>NEW REQUEST</a>

<section class="abs panel" style="left:850px;top:569px;width:334px;height:147px">
  <div class="panel-head">Recent Completed Requests</div>
  <table class="grid"><colgroup><col style="width:163px"><col></colgroup>
    <tr><th style="padding-left:16px">Request No.</th><th>Completed Date</th></tr>
    <tr><td style="padding-left:16px">56-0003</td><td>20/4/2013</td></tr>
    <tr><td style="padding-left:16px">56-0003</td><td>21/4/2013</td></tr>
  </table>
  <div class="pager" style="height:39px">
    <span class="pbtn pfirst" style="margin-right:21px"><svg width="20" height="14"><path d="M10 1L4 7l6 6M17 1l-6 6 6 6" stroke="#555" stroke-width="2.5" fill="none"/></svg></span>
    <span class="pbtn"><svg width="12" height="14"><path d="M9 1L3 7l6 6" stroke="#555" stroke-width="2.5" fill="none"/></svg></span>
    <span class="pinfo">Page <span class="pbox">1</span> of 1</span>
    <span class="pbtn"><svg width="12" height="14"><path d="M3 1l6 6-6 6" stroke="#555" stroke-width="2.5" fill="none"/></svg></span>
    <span class="pbtn plast"><svg width="20" height="14"><path d="M3 1l6 6-6 6M10 1l6 6-6 6" stroke="#555" stroke-width="2.5" fill="none"/></svg></span>
  </div>
</section>

<p class="abs footer">© 2013 | Norvane Petrochemicals. All rights reserved</p>
<div class="abs social" aria-label="Social links"><span></span><span></span><span></span><span></span></div>

</div>
</body>
</html>
```